Business card design for web travel company

Hi
we'd like to receive some proposal for a business card design.
Stayvora is a private travel club, dedicated to all travel lovers, with unique offers for exclusive destinations all around the world. At Stayvora you can find a wide range of offers for resorts, boutique hotels and travel packages at the best guaranteed price available on the market. The convenience of the offer is guaranteed by a private sales model: offers are available for a limited time only and they are personally chosen by Stayvora's qualified team of travel experts.
We offer only exclusive hotels with discounted prices but we are not an outlet or a discount supermarket: the design should reflect our connection with luxury, exclusivity using the same style of our website www.stayvora-example.com.
We want to make sure that when we'll present ourself to our business partner they will feel immediately which is our brand positioning giving them also a sense of an affordable and reliable partner.
In attachment you can also find our brand guidelines (please note that we are NOT USING ANY MORE THE TAG LINE "Five star outlet" mentioned in it).
The info to be inserted are:
Name Surname
Job Title
Tel
Mobile (when needed)
Email
Stayvora S.r.l.
Via Bruno Salvi 27
20139 Milano

```html
<!DOCTYPE html>
<html lang="en">
<head>
<meta charset="utf-8">
<title>Stayvora — Business Card</title>
<link rel="stylesheet" href="https://fonts.googleapis.com/css2?family=Roboto:wght@300;400;700&display=swap">
<style>
  :root {
    --backdrop: #e9e6e1;
    --card-dark: #050505;
    --card-gold: #bdb07a;
    --card-gold-edge: #6d6446;
    --gold: #bfae79;
    --ink-light: #ffffff;
    --ink-muted: #cfcfcf;
    --ink-dark: #141414;
  }
  * { margin: 0; padding: 0; box-sizing: border-box; }
  html, body {
    width: 1200px;
    height: 900px;
    overflow: hidden;
    background: var(--backdrop);
    font-family: "Roboto", Arial, sans-serif;
  }
  .sheet {
    position: relative;
    width: 1200px;
    height: 900px;
  }
  .card {
    position: absolute;
    top: 307px;
    width: 502px;
    height: 288px;
    border-radius: 12px;
    overflow: hidden;
  }
  .card--front {
    left: 75px;
    background: var(--card-dark);
    color: var(--ink-light);
  }
  .card--back {
    left: 627px;
    background: var(--card-gold);
    border: 1px solid var(--card-gold-edge);
    color: var(--ink-dark);
  }
  .brand-name {
    position: absolute;
    font-weight: 300;
    font-size: 48px;
    letter-spacing: 0.5px;
    line-height: 1;
  }
  .card--front .brand-name { left: 30px; top: 45px; color: var(--ink-light); }
  .card--back .brand-name { left: 31px; top: 123px; color: var(--ink-dark); }
  .holder {
    position: absolute;
    left: 285px;
    right: 20px;
    top: 172px;
  }
  .holder-name {
    font-weight: 700;
    font-size: 22px;
    line-height: 26px;
  }
  .holder-role {
    font-weight: 300;
    font-size: 12.5px;
    line-height: 16px;
    color: var(--gold);
    margin-bottom: 10px;
  }
  .contact-line {
    display: flex;
    align-items: center;
    gap: 6px;
    font-size: 12.5px;
    font-weight: 400;
    line-height: 19px;
    white-space: nowrap;
  }
  .contact-line svg { width: 13px; height: 11px; flex: none; }
  .website {
    position: absolute;
    right: 28px;
    top: 146px;
    font-size: 14px;
    font-weight: 400;
    letter-spacing: 2px;
  }
  .company-address {
    position: absolute;
    right: 28px;
    bottom: 24px;
    font-style: normal;
    font-size: 11.5px;
    font-weight: 400;
    line-height: 16px;
    letter-spacing: 0.5px;
    text-align: right;
  }
</style>
</head>
<body>
<main class="sheet">
  <section class="card card--front" aria-label="Card front">
    <div class="brand-name">Stayvora</div>
    <div class="holder">
      <div class="holder-name">Marco Ferlini</div>
      <div class="holder-role">Partnership Manager</div>
      <div class="contact-line">
        <svg viewBox="0 0 13 11" aria-hidden="true"><path d="M1 4 Q6.5 0 12 4 L10.5 5.5 L8.5 4.5 L8.5 3.5 Q6.5 3 4.5 3.5 L4.5 4.5 L2.5 5.5 Z M3 6 L10 6 L11 10 L2 10 Z" fill="var(--gold)"/></svg>
        <span>: +39 0200 5555</span>
      </div>
      <div class="contact-line">
        <svg viewBox="0 0 13 11" aria-hidden="true"><rect x="1" y="1.5" width="11" height="8" fill="none" stroke="var(--gold)" stroke-width="1.2"/><path d="M1 1.5 L6.5 6 L12 1.5 M1 9.5 L5 5 M12 9.5 L8 5" fill="none" stroke="var(--gold)" stroke-width="1"/></svg>
        <span>: marco@stayvora-example.com</span>
      </div>
    </div>
  </section>

  <section class="card card--back" aria-label="Card back">
    <div class="brand-name">Stayvora</div>
    <div class="website">www.stayvora-example.com</div>
    <address class="company-address">
      Stayvora S.r.l.<br>
      Via Bruno Salvi 27<br>
      20139 Milano
    </address>
  </section>
</main>
</body>
</html>
```